Design a web site for my business - Brightline Coatings Co.

We are a family business that handles design, fabrication and installation of powder coated aluminum, stainless steel and glass products. Including handrails, privacy slat screens, electric gates and pool fencing. We are based in the Whitsundays in North Queensland and service an area from Airlie Beach to Townsville.

Target Market(s)

Domestic and commercial

Industry/Entity Type

fabrication - manufacturing

Coding

Coded - Design and coding required

Number of Pages Required

5+ page

Colors
0054AA
0677BA
7BADD7
CADEEF
E8F1F8

Requirements
Must have
• photo galleries, contact page, one page for privacy screens, balustrades, glass fencing, stainless steel handrail, powder coated aluminium handrails and pool fencing

```html
<!DOCTYPE html>
<html lang="en">
<head>
<meta charset="utf-8">
<title>Brightline Coatings Co — Custom Metal &amp; Glass Solutions</title>
<link href="https://fonts.googleapis.com/css2?family=Raleway:wght@500;600;700&family=Roboto:wght@400;500;700&display=swap" rel="stylesheet">
<style>
:root{
  --navy:#0054AA;
  --blue:#0677BA;
  --sky:#7BADD7;
  --mist:#CADEEF;
  --ice:#E8F1F8;
  --ink:#333;
  --white:#fff;
  --star:#e8563a;
}
*{box-sizing:border-box;margin:0;padding:0}
html,body{width:1200px;height:5051px;overflow:hidden}
body{position:relative;background:var(--white);font-family:"Roboto",Arial,sans-serif;color:var(--ink)}
.abs{position:absolute}
.heading{font-family:"Raleway",Arial,sans-serif;font-weight:600;color:var(--navy);font-size:40px;line-height:48px;letter-spacing:.5px}
.heading.center{left:0;width:1200px;text-align:center}
.heading.center::after{content:"";display:block;width:80px;height:3px;background:currentColor;margin:4px auto 0}
.btn{position:absolute;display:flex;align-items:center;justify-content:center;background:var(--blue);color:#fff;font:500 15px "Roboto",sans-serif;text-transform:uppercase}
.photo{position:absolute}

/* header */
.site-header{position:absolute;left:0;top:0;width:1200px;height:143px;background:#fff;z-index:3}
.brand{position:absolute;left:59px;top:0;width:255px;height:178px;background:#fff;clip-path:polygon(0 0,100% 0,100% 72%,85% 100%,15% 100%,0 85%);z-index:4;display:flex;align-items:center;justify-content:center;flex-direction:column;gap:10px}
.brand-dot{width:46px;height:46px;border-radius:50%;background:var(--blue)}
.brand-name{font:700 17px "Raleway",sans-serif;color:var(--navy);text-align:center;white-space:nowrap}
.phone{left:692px;top:30px;font-size:17px;color:var(--navy);display:flex;align-items:center;gap:10px}
.quote{left:896px;top:18px;width:192px;height:46px;background:var(--ice);color:var(--navy);font:500 15px Roboto,sans-serif;display:flex;align-items:center;justify-content:center;text-transform:uppercase}
.nav{left:423px;top:98px;display:flex;gap:30px;font:500 14px Roboto,sans-serif;color:var(--navy)}
.nav .active{text-decoration:underline;text-underline-offset:5px}
.nav-sep{left:935px;top:86px;width:1px;height:44px;background:var(--mist)}
.socials{display:flex;gap:10px}
.social{width:34px;height:34px;border-radius:50%;background:var(--ice);box-shadow:0 1px 4px rgba(0,0,0,.15)}
.social.on{background:var(--blue)}

/* hero */
.hero{left:0;top:143px;width:1200px;height:730px;background:linear-gradient(160deg,#7d8a96 0%,#5f6f74 35%,#4e5a56 60%,#6b6f78 100%)}
.hero-title{right:112px;top:310px;text-align:right;font:700 40px/48px "Roboto",sans-serif;color:#fff;text-transform:uppercase}
.hero-text{right:112px;top:463px;width:530px;text-align:right;font:400 19px/27px Roboto,sans-serif;color:#fff}
.hero-btn{left:931px;top:567px;width:157px;height:47px;background:#fff;color:var(--navy);font:500 15px Roboto,sans-serif;display:flex;align-items:center;justify-content:center}
.dots{left:1141px;top:430px;display:flex;flex-direction:column;gap:9px}
.dots i{width:12px;height:12px;border-radius:50%;border:2px solid #fff;display:block}
.dots i.on{background:#fff}

/* about */
.about-text{left:112px;top:1066px;width:430px;font:400 15px/26px Roboto,sans-serif;color:var(--ink);text-align:justify}
.about-text p+p{margin-top:14px}
.frame{left:731px;top:1131px;width:357px;height:316px;border:10px solid var(--navy);border-left:none;border-top:none}
.frame::before{content:"";position:absolute;top:0;width:72px;height:10px;background:var(--navy);left:285px}
.frame::after{content:"";position:absolute;left:0;bottom:-10px;width:10px;height:60px;background:var(--navy)}

/* services */
.services{left:0;top:1563px;width:1200px;height:937px;background:var(--ice)}
.tile{position:absolute;width:474px;height:298px;display:flex;align-items:center;justify-content:center;font:700 22px Roboto,sans-serif;color:#fff;text-transform:uppercase}

/* testimonials */
.card{position:absolute;top:2761px;width:300px;height:329px;background:#fff;border-radius:10px;padding:22px 34px}
.quote-mark{font:700 52px/40px Georgia,serif;color:#333}
.stars{color:var(--star);font-size:20px;letter-spacing:2px;margin:4px 0 12px}
.card p{font:400 14px/22px Roboto,sans-serif;color:#444}
.rule{width:40px;height:1px;background:var(--star);margin:16px 0 8px}
.author{font:500 14px Roboto,sans-serif;color:#222}

/* contact */
.contact{left:0;top:4147px;width:1200px;height:514px;background:var(--ice)}
.field{position:absolute;left:180px;width:408px;height:50px;background:#fff;border-radius:25px;display:flex;align-items:center;font:400 15px Roboto,sans-serif;color:#444}
.field .ico{width:56px;height:100%;border-right:1px solid var(--mist);display:flex;align-items:center;justify-content:center}
.field span{padding-left:14px}
.message{left:606px;top:4316px;width:412px;height:178px;background:#fff;border-radius:22px;padding:18px 0 0 0;display:flex;align-items:flex-start;font:400 15px Roboto,sans-serif;color:#444}

/* footer */
.footer{left:0;top:4661px;width:1200px;height:390px;background:var(--navy)}
.foot-h{font:500 15px Roboto,sans-serif;color:#fff;text-transform:uppercase}
.foot-h::after{content:"";display:block;width:110px;height:1px;background:#fff;margin-top:10px}
.foot-links{font:400 14px/39px Roboto,sans-serif;color:#fff}
.contact-row{display:flex;gap:16px;align-items:flex-start;font:400 14px/21px Roboto,sans-serif;color:#fff;margin-bottom:16px}
.contact-row .ico{width:38px;height:38px;border-radius:50%;background:#fff;flex:none;display:flex;align-items:center;justify-content:center}
.news{left:830px;top:4813px;width:258px;height:46px;background:#fff;display:flex;align-items:center;justify-content:space-between;padding:0 18px;font:400 14px Roboto,sans-serif;color:#444}
.copy{left:0;top:5003px;width:1200px;text-align:center;font:400 13px Roboto,sans-serif;color:#fff}
.foot-line{left:112px;top:4990px;width:976px;height:1px;background:rgba(255,255,255,.25)}
</style>
</head>
<body>

<!-- Header -->
<header class="site-header">
  <div class="abs phone">
    <svg width="16" height="16" viewBox="0 0 24 24"><path fill="#0054AA" d="M6.6 10.8a15 15 0 006.6 6.6l2.2-2.2c.3-.3.7-.4 1-.2 1.1.4 2.3.6 3.6.6.6 0 1 .4 1 1V20c0 .6-.4 1-1 1A17 17 0 013 4c0-.6.4-1 1-1h3.5c.6 0 1 .4 1 1 0 1.3.2 2.5.6 3.6.1.3 0 .7-.2 1z"/></svg>
    +61 400 555 218
  </div>
  <div class="abs quote">Get a free quote</div>
  <nav class="abs nav">
    <span class="active">HOME</span><span>ABOUT US</span><span>SERVICES</span><span>PROJECTS</span><span>CONTACT US</span>
  </nav>
  <div class="abs nav-sep"></div>
  <div class="abs socials" style="left:970px;top:90px">
    <span class="social" aria-label="Social link"></span>
    <span class="social on" aria-label="Social link"></span>
    <span class="social" aria-label="Social link"></span>
  </div>
</header>
<div class="brand">
  <span class="brand-dot"></span>
  <span class="brand-name">Brightline Coatings Co</span>
</div>

<!-- Hero -->
<section class="abs hero" role="img" aria-label="Waterfront boardwalk with powder-coated balustrade beside the sea, palm trees and flowering trees"></section>
<svg class="abs" style="left:0;top:740px" width="1200" height="134" viewBox="0 740 1200 134">
  <polygon points="640,873 1200,742 1200,873" fill="#0054AA"/>
  <polygon points="0,873 1088,750 1200,873" fill="#fff"/>
</svg>
<h1 class="abs hero-title">Custom metal &amp;<br>glass solutions<br>that last.</h1>
<p class="abs hero-text">Creating durable, stylish, and low-maintenance products for homes, businesses, and commercial developments throughout North Queensland.</p>
<div class="abs hero-btn">GET STARTED</div>
<div class="abs dots"><i></i><i class="on"></i><i></i><i></i></div>

<!-- About -->
<h2 class="abs heading" style="left:112px;top:985px">ABOUT US</h2>
<div class="abs" style="left:112px;top:1034px;width:140px;height:2px;background:var(--navy)"></div>
<div class="abs about-text">
  <p>We are a family-owned fabrication and installation company specialising in premium powder-coated aluminium, stainless steel, and glass products. With a commitment to quality workmanship and exceptional customer service, we design, manufacture, and install custom solutions tailored to your property.</p>
  <p>Based in the Whitsundays, we proudly service clients from Airlie Beach to Townsville, delivering durable, stylish, and compliant products for residential and commercial projects.</p>
</div>
<div class="btn" style="left:112px;top:1346px;width:149px;height:46px">LEARN MORE</div>
<div class="abs frame"></div>
<div class="photo" style="left:718px;top:955px;width:292px;height:329px;background:linear-gradient(170deg,#7f95b3,#4d4a44 55%,#3f5238)" role="img" aria-label="Elevated timber house with steel balustrade deck among tropical plants"></div>
<div class="photo" style="left:629px;top:1124px;width:218px;height:243px;background:linear-gradient(180deg,#5a86c7,#cdd3d6 60%,#9a9a96);border:2px solid #fff" role="img" aria-label="White slat gate and pool fence beside concrete steps"></div>

<!-- Services -->
<section class="abs services"></section>
<h2 class="heading center abs" style="top:1636px">OUR SERVICES</h2>
<div class="tile" style="left:112px;top:1728px;background:linear-gradient(180deg,#6c8fc3 0%,#9aa5ae 45%,#5d5c58 70%,#7d7770)" role="img" aria-label="Privacy slat screen along a suburban driveway">PRIVACY SCREENS</div>
<div class="tile" style="left:614px;top:1728px;background:linear-gradient(180deg,#7BADD7,#0677BA 60%,#0054AA)" role="img" aria-label="Pool fencing beside a modern house">POOL FENCING</div>
<div class="tile" style="left:112px;top:2053px;background:linear-gradient(160deg,#3f5a34,#6f8a6a 50%,#9fa7a0)" role="img" aria-label="Frameless glass fencing among tropical plants">GLASS FENCING</div>
<div class="tile" style="left:614px;top:2053px;background:linear-gradient(160deg,#d8d8d6,#9a9893 50%,#7b5434)" role="img" aria-label="Black steel balustrade on a timber staircase">BALUSTRADES</div>
<div class="btn" style="left:504px;top:2404px;width:192px;height:47px">VIEW ALL SERVICES</div>

<!-- Testimonials -->
<svg class="abs" style="left:0;top:2510px" width="1200" height="690" viewBox="0 2510 1200 690">
  <polygon points="150,2665 600,2514 1050,2665" fill="#0054AA"/>
  <rect x="0" y="2660" width="1200" height="537" fill="#0054AA"/>
  <polygon points="170,2661 600,2548 1030,2661" fill="#fff"/>
</svg>
<h2 class="heading center abs" style="top:2664px;color:#fff">TESTIMONIALS</h2>
<div class="card" style="left:112px">
  <div class="quote-mark">&ldquo;</div><div class="stars">★★★★★</div>
  <p>Lorem ipsum dolor sit amet, conse ctetur adipiscing elit, sed do eiusm od tempor incididunt ut labore et dolore magna aliqua. Ut enim ad minim veniam, quis nostrud exercitatio n ullamco laboris nisi ut aliquip ex ea consequat.</p>
  <div class="rule"></div><div class="author">- John Doe</div>
</div>
<div class="card" style="left:451px">
  <div class="quote-mark">&ldquo;</div><div class="stars">★★★★★</div>
  <p>Lorem ipsum dolor sit amet, conse ctetur adipiscing elit, sed do eiusm od tempor incididunt ut labore et dolore magna aliqua. Ut enim ad minim veniam, quis nostrud exercitatio n ullamco laboris nisi ut aliquip ex ea consequat.</p>
  <div class="rule"></div><div class="author">- John Doe</div>
</div>
<div class="card" style="left:788px">
  <div class="quote-mark">&ldquo;</div><div class="stars">★★★★★</div>
  <p>Lorem ipsum dolor sit amet, conse ctetur adipiscing elit, sed do eiusm od tempor incididunt ut labore et dolore magna aliqua. Ut enim ad minim veniam, quis nostrud exercitatio n ullamco laboris nisi ut aliquip ex ea consequat.</p>
  <div class="rule"></div><div class="author">- John Doe</div>
</div>
<svg class="abs" style="left:560px;top:3132px" width="80" height="10">
  <circle cx="8" cy="5" r="3" fill="#7BADD7"/><circle cx="24" cy="5" r="3" fill="#7BADD7"/><circle cx="40" cy="5" r="3" fill="#7BADD7"/><circle cx="56" cy="5" r="3.5" fill="#fff"/><circle cx="72" cy="5" r="3" fill="#7BADD7"/>
</svg>

<!-- Projects -->
<h2 class="heading center abs" style="top:3308px">LATEST PROJECTS</h2>
<svg class="abs" style="left:112px;top:3404px" width="976" height="616" viewBox="0 0 976 616">
  <defs>
    <linearGradient id="p1" x1="0" y1="0" x2="0" y2="1"><stop offset="0" stop-color="#3f6fbf"/><stop offset=".5" stop-color="#c9c4b4"/><stop offset=".8" stop-color="#4a4a48"/><stop offset="1" stop-color="#7aa24a"/></linearGradient>
    <linearGradient id="p2" x1="0" y1="0" x2="1" y2="1"><stop offset="0" stop-color="#3d5a2e"/><stop offset=".5" stop-color="#8a7a66"/><stop offset="1" stop-color="#6d8a5a"/></linearGradient>
    <linearGradient id="p3" x1="0" y1="0" x2="0" y2="1"><stop offset="0" stop-color="#2f64c6"/><stop offset=".5" stop-color="#e7e6e0"/><stop offset="1" stop-color="#b9b2a0"/></linearGradient>
    <linearGradient id="p4" x1="0" y1="0" x2="0" y2="1"><stop offset="0" stop-color="#cfcfcb"/><stop offset=".5" stop-color="#8a8e8e"/><stop offset="1" stop-color="#aab8c0"/></linearGradient>
    <linearGradient id="p5" x1="0" y1="0" x2="0" y2="1"><stop offset="0" stop-color="#2d62c2"/><stop offset=".55" stop-color="#e4e1da"/><stop offset="1" stop-color="#6e8a3e"/></linearGradient>
  </defs>
  <g role="img" aria-label="Gallery of completed fencing, screen, balustrade and glass projects">
    <polygon points="0,0 425,0 510,298 0,298" fill="url(#p1)"/>
    <polygon points="440,0 976,0 976,298 525,298" fill="url(#p2)"/>
    <rect x="0" y="316" width="298" height="300" fill="url(#p3)"/>
    <polygon points="315,316 710,316 584,616 315,616" fill="url(#p4)"/>
    <polygon points="726,316 976,316 976,616 600,616" fill="url(#p5)"/>
  </g>
</svg>

<!-- Contact -->
<section class="abs contact"></section>
<h2 class="heading center abs" style="top:4224px">CONTACT US</h2>
<div class="field" style="top:4320px"><span class="ico"><svg width="14" height="16" viewBox="0 0 14 16"><circle cx="7" cy="4.5" r="4" fill="#0677BA"/><path d="M0 16c0-4 3-6.5 7-6.5s7 2.5 7 6.5z" fill="#0677BA"/></svg></span><span>Your Name</span></div>
<div class="field" style="top:4386px"><span class="ico"><svg width="16" height="12" viewBox="0 0 16 12"><rect width="16" height="12" rx="1" fill="#0677BA"/><path d="M0 1l8 6 8-6" stroke="#fff" stroke-width="1.4" fill="none"/></svg></span><span>Email</span></div>
<div class="field" style="top:4451px"><span class="ico"><svg width="14" height="14" viewBox="0 0 24 24"><path fill="#0677BA" d="M6.6 10.8a15 15 0 006.6 6.6l2.2-2.2c.3-.3.7-.4 1-.2 1.1.4 2.3.6 3.6.6.6 0 1 .4 1 1V20c0 .6-.4 1-1 1A17 17 0 013 4c0-.6.4-1 1-1h3.5c.6 0 1 .4 1 1 0 1.3.2 2.5.6 3.6.1.3 0 .7-.2 1z"/></svg></span><span>Phone</span></div>
<div class="abs message"><span style="width:56px;height:26px;border-right:1px solid #CADEEF;display:flex;align-items:center;justify-content:center"><svg width="16" height="13" viewBox="0 0 16 13"><ellipse cx="7" cy="5" rx="7" ry="5" fill="#0677BA"/><path d="M3 8l-1 5 5-3z" fill="#0677BA"/></svg></span><span style="padding-left:14px">Your Message</span></div>
<div class="btn" style="left:514px;top:4526px;width:172px;height:43px">SEND MESSAGE</div>

<!-- Footer -->
<footer class="abs footer"></footer>
<div class="abs" style="left:100px;top:4820px;display:flex;flex-direction:column;align-items:center;gap:12px;width:230px">
  <span style="width:50px;height:50px;border-radius:50%;background:#fff"></span>
  <span style="font:700 18px Raleway,sans-serif;color:#fff;text-align:center;white-space:nowrap">Brightline Coatings Co</span>
</div>
<div class="abs" style="left:375px;top:4727px;width:250px">
  <div class="foot-h">Contact Us</div>
  <div style="margin-top:22px">
    <div class="contact-row"><span class="ico"><svg width="12" height="16" viewBox="0 0 12 16"><path d="M6 0a6 6 0 016 6c0 4.5-6 10-6 10S0 10.5 0 6a6 6 0 016-6z" fill="#0054AA"/><circle cx="6" cy="6" r="2.2" fill="#fff"/></svg></span><span>12 Harbour View Rd, Cannonvale, QLD, Australia, Queensland</span></div>
    <div class="contact-row"><span class="ico"><svg width="14" height="14" viewBox="0 0 24 24"><path fill="#0054AA" d="M6.6 10.8a15 15 0 006.6 6.6l2.2-2.2c.3-.3.7-.4 1-.2 1.1.4 2.3.6 3.6.6.6 0 1 .4 1 1V20c0 .6-.4 1-1 1A17 17 0 013 4c0-.6.4-1 1-1h3.5c.6 0 1 .4 1 1 0 1.3.2 2.5.6 3.6.1.3 0 .7-.2 1z"/></svg></span><span>Call Us:<br>+61 400 555 218</span></div>
    <div class="contact-row"><span class="ico"><svg width="14" height="11" viewBox="0 0 16 12"><rect width="16" height="12" rx="1" fill="#0054AA"/><path d="M0 1l8 6 8-6" stroke="#fff" stroke-width="1.4" fill="none"/></svg></span><span style="font-size:13px">Email Us:<br><u>hello@brightlinecoatings.example</u></span></div>
  </div>
</div>
<div class="abs" style="left:653px;top:4727px">
  <div class="foot-h">Quick Links</div>
  <div class="foot-links" style="margin-top:12px">Home<br>About Us<br>Services<br>Projects<br>Contact Us</div>
</div>
<div class="abs" style="left:830px;top:4727px">
  <div class="foot-h">Newsletter</div>
</div>
<div class="abs news"><span>Email Address</span><svg width="15" height="15" viewBox="0 0 16 16"><path d="M16 0L0 7l5 2 2 6 3-4 4 3z" fill="#0677BA"/></svg></div>
<div class="abs socials" style="left:830px;top:4879px">
  <span class="social" style="width:32px;height:32px;background:#7BADD7"></span>
  <span class="social" style="width:32px;height:32px;background:#fff"></span>
  <span class="social" style="width:32px;height:32px;background:#fff"></span>
</div>
<div class="abs foot-line"></div>
<div class="abs copy">Copyright © 2026 &nbsp;/&nbsp; All Rights Reserved &nbsp;/&nbsp; Privacy Policy</div>

</body>
</html>
```